Software Development Consulting Company Needs Business Card Design

We need a new business card design for our consultants at Kestrel Works (kestrelworks.example). We are a small firm that provides high-end software development and methodology consulting to medium to large enterprise IT organizations.

Our logo uses Futura for the font and we would like to stick with navy blue and canary yellow for the logo colors. Attached are normal and reversed versions of our logos in illustrator format.
Updates

Hi Everyone, Thank yo very much for your amazing design ideas. I have created a poll for this project and our employees will be voting on the design they wish to use. We will be making a decision this Wednesday (October 22nd). Thanks again, Dale Hartwick

Industry/Entity Type

Business

```html
<!DOCTYPE html>
<html lang="en">
<head>
<meta charset="utf-8">
<title>Kestrel Works – Business Card</title>
<link rel="stylesheet" href="https://fonts.googleapis.com/css2?family=Source+Sans+3:wght@400;600&display=swap">
<style>
  :root {
    --navy: #1c4a6e;
    --canary: #ffee00;
    --white: #ffffff;
    --backdrop: #e9eaee;
    --card-w: 770px;
    --card-h: 440px;
  }
  * { box-sizing: border-box; margin: 0; padding: 0; }
  html, body {
    width: 1200px; height: 980px; overflow: hidden;
    background: var(--backdrop);
    font-family: "Source Sans 3", "Myriad Pro", sans-serif;
    color: var(--navy);
  }
  .card {
    position: absolute; left: 215px;
    width: var(--card-w); height: var(--card-h);
    border-radius: 26px; overflow: hidden;
    box-shadow: 0 6px 18px rgba(0,0,0,.15);
  }
  .card--front { top: 30px; background: var(--white); }
  .card--back { top: 510px; background: var(--canary); }

  .wordmark {
    position: absolute; left: 0; right: 0; text-align: center;
    font-family: "Source Sans 3", "Myriad Pro", sans-serif; font-weight: 600;
    color: var(--navy); letter-spacing: 2px; line-height: 1;
  }
  .card--front .wordmark { top: 54px; font-size: 50px; }

  .band--yellow { position: absolute; left: 0; right: 0; top: 160px; height: 220px; background: var(--canary); }
  .band--navy { position: absolute; left: 0; right: 0; top: 380px; bottom: 0; background: var(--navy); }

  .contact { position: absolute; top: 190px; left: 0; right: 0; display: flex; }
  .contact__person { width: 340px; text-align: right; padding-right: 22px; line-height: 1.25; }
  .contact__name { font-size: 30px; font-weight: 600; }
  .contact__title, .contact__place { font-size: 20px; }
  .contact__divider { width: 2px; height: 150px; background: var(--navy); }
  .contact__lines { list-style: none; padding-left: 22px; padding-top: 34px; font-size: 21px; line-height: 1.5; }
  .contact__lines li { display: flex; align-items: center; gap: 10px; white-space: nowrap; }
  .contact__lines svg { width: 20px; height: 20px; flex: none; }

  .strip-name { position: absolute; top: 396px; left: 110px; color: var(--white); font-size: 26px; font-weight: 600; line-height: 1.2; }
  .strip-name span { font-weight: 400; font-size: 22px; }

  .card--back .wordmark { top: 150px; font-size: 58px; }
  .back-url { position: absolute; top: 272px; left: 0; right: 0; text-align: center; font-size: 26px; letter-spacing: 4px; }
</style>
</head>
<body>
  <section class="card card--front">
    <p class="wordmark">Kestrel Works</p>
    <div class="band--yellow"></div>
    <div class="band--navy"></div>
    <div class="contact">
      <div class="contact__person">
        <p class="contact__name">Your Name</p>
        <p class="contact__title">Title</p>
        <p class="contact__place">Lakeport + Fairview, IL</p>
      </div>
      <div class="contact__divider"></div>
      <ul class="contact__lines">
        <li><svg viewBox="0 0 20 20"><circle cx="10" cy="10" r="9" fill="none" stroke="#1c4a6e" stroke-width="1.6"/><path d="M7 5l2 2-1 1.5c.6 1.4 1.6 2.4 3 3L12.5 10l2 2-1.5 2C9 13.5 6.5 11 6 6.5z" fill="#1c4a6e"/></svg>555-010-4827</li>
        <li><svg viewBox="0 0 20 20"><rect x="2" y="5" width="16" height="11" rx="1.5" fill="#1c4a6e"/><path d="M3 6l7 5 7-5" fill="none" stroke="#ffee00" stroke-width="1.4"/></svg>info@kestrelworks.example</li>
        <li><svg viewBox="0 0 20 20" fill="none" stroke="#1c4a6e" stroke-width="1.5"><circle cx="10" cy="10" r="8"/><ellipse cx="10" cy="10" rx="3.5" ry="8"/><path d="M2 10h16M3.5 6h13M3.5 14h13"/></svg>www.kestrelworks.example</li>
      </ul>
    </div>
    <p class="strip-name">Your Name, <span>Title</span></p>
  </section>

  <section class="card card--back">
    <p class="wordmark">Kestrel Works</p>
    <p class="back-url">www.kestrelworks.example</p>
  </section>
</body>
</html>
```